THE KINDRED LANTERN

project description

The Kindred Lantern was created to challenge the lack of meaning and values in power of mainstream media.

This website will be a platform through which you can explore the meaning of humanity, through a variety of lenses - philosophy, politics, science, art, human interest stories, etc.

As an organization, TKL aims to further the understanding of the meaning of humanity, including its spiritual and existential challenges in 21st century. We wish to inspire and develop this understanding, while transforming mass media and “visual” spaces so they display the beauty and interconnectedness of human beings.

We believe that the kindred lantern and that our “visual” space and mass media should reflect and support those values.

We are looking to create an image that may be seen on the site independently, full screen - or as the background to the home page (with text on top of it, potentially.)
Updates

 

 The city/the background with the advertisementshouldn’t be to depressing because (indigo blue or light gray color) so overall, the page has a pleasant soft look and feel.

 

Also place the boy is looking at needs to have advertisement

 

Thank you

Target Market(s)

people that are sophisticated, modern, engage, care, awere, who are interested scholarly discussions of media, philosophy,art/desighn community - as well as the human spirit.

Industry/Entity Type

Media

Requirements
Must have
• I have photos of a boy looking up. I would like to take this image (pick one) and incorporate into a city scene - one with buildings littered with mass media information and adds - similar to the look of NYC's Vell Plaza. He is looking up a bit overwhelmed trying to make sense of the world he is seeing.
Nice to have
• However, the city scene in the background may be sketched or distorted
Should not have
• should not be agresive or too busy

```html
<!DOCTYPE html>
<html lang="en">
<head>
<meta charset="utf-8">
<title>The Kindred Lantern</title>
<link rel="stylesheet" href="https://fonts.googleapis.com/css2?family=Roboto+Condensed:wght@400;700&family=Open+Sans:wght@400;700&display=swap">
<style>
  :root {
    --page: #000000;
    --bar: #111111;
    --panel: #1a1b1d;
    --text: #e6e6e6;
    --muted: #9a9a9a;
    --white: #ffffff;
    --accent: #e10a0a;
    --accent-dark: #b00000;
  }
  * { margin: 0; padding: 0; box-sizing: border-box; }
  html, body { width: 1200px; height: 900px; overflow: hidden; background: var(--page); }
  .canvas { position: relative; width: 1200px; height: 900px; background: var(--page); font-family: "Open Sans", Arial, sans-serif; color: var(--text); }

  .topbar { position: absolute; left: 0; top: 158px; width: 1200px; height: 30px; background: linear-gradient(#0a0a0a, #181818); border-bottom: 2px solid #d8d8d8; }
  .brand { position: absolute; left: 297px; top: 9px; font-family: "Roboto Condensed", Arial, sans-serif; font-weight: 700; font-size: 10px; color: var(--white); letter-spacing: .2px; }
  .brand .sep { color: var(--muted); margin: 0 6px; font-weight: 400; }
  .nav { position: absolute; right: 318px; top: 9px; display: flex; align-items: center; font-family: "Roboto Condensed", Arial, sans-serif; font-weight: 700; font-size: 8.5px; color: var(--white); }
  .nav .item { padding: 0 9px; border-left: 1px solid #777; line-height: 9px; }
  .nav .item:first-child { border-left: 0; }
  .social { display: flex; gap: 4px; margin-left: 5px; }
  .social span { width: 9px; height: 9px; background: #4a7fc0; display: block; }

  .hero-backdrop { position: absolute; left: 0; top: 188px; width: 1200px; height: 174px;
    background: linear-gradient(90deg, #1c1d20 0%, #2a2c30 20%, #1d1f22 45%, #26282c 75%, #1a1b1e 100%); }
  .content { position: absolute; left: 0; top: 188px; width: 1200px; height: 174px; }
  .col { position: absolute; top: 15px; }
  .col h2 { font-family: "Roboto Condensed", Arial, sans-serif; font-weight: 700; font-size: 9.5px; color: var(--white); margin-bottom: 2px; letter-spacing: .2px; }
  .col p { font-size: 6.4px; line-height: 9px; color: var(--text); margin-bottom: 9px; }
  .col-welcome { left: 297px; width: 216px; }
  .col-work { left: 529px; width: 152px; }
  .col-work h2.second { margin-top: 11px; }
  .col-video { left: 732px; width: 172px; }

  .player { margin-top: 4px; width: 170px; height: 106px; background: #0c0c0c; border: 1px solid #333; padding: 2px; }
  .player .screen { width: 164px; height: 87px; background: linear-gradient(135deg, #3b4f66 0%, #6b4a3c 40%, #2d3c52 70%, #5a3b40 100%); position: relative; }
  .player .screen .play { position: absolute; left: 66px; top: 28px; }
  .player .screen .label { position: absolute; width: 100%; top: 76px; text-align: center; font-family: "Roboto Condensed", Arial, sans-serif; font-weight: 700; font-size: 8px; color: #bbbbbb; }
  .player .controls { height: 12px; margin-top: 2px; background: linear-gradient(#dadada, #9c9c9c); display: flex; align-items: center; padding: 0 4px; gap: 5px; font-size: 6.5px; color: #111; }
  .player .track { width: 62px; height: 3px; background: #555; }
  .player .track i { display: block; width: 22px; height: 3px; background: #111; }

  .divider-red { position: absolute; left: 0; top: 361px; width: 1200px; height: 2px; background: var(--accent); }
  .close-tab { position: absolute; left: 539px; top: 362px; width: 95px; height: 21px; background: linear-gradient(var(--accent), var(--accent-dark)); border-radius: 0 0 3px 3px; font-size: 6.5px; color: var(--white); display: flex; align-items: center; justify-content: center; gap: 6px; z-index: 2; }

  .city { position: absolute; left: 0; top: 363px; width: 1200px; height: 277px;
    background: linear-gradient(90deg, #4b5058 0%, #8a8f98 22%, #c9cbcf 42%, #a7a9ad 55%, #6e6356 72%, #8d6c4c 88%, #5b4f45 100%); }
  .city::after { content: ""; position: absolute; inset: 0; background: linear-gradient(rgba(40,50,70,.25), rgba(255,255,255,0) 50%, rgba(120,100,70,.35)); }
  .divider-white { position: absolute; left: 0; top: 639px; width: 1200px; height: 3px; background: #e8e8e8; }

  .footer { position: absolute; left: 0; top: 642px; width: 1200px; height: 100px; background: radial-gradient(ellipse 180px 60px at 600px 40px, #222 0%, #000 100%); }
  .footer-mark { position: absolute; left: 478px; top: 14px; display: flex; align-items: flex-start; gap: 10px; }
  .footer-mark .initials { font-family: "Roboto Condensed", Arial, sans-serif; font-weight: 700; font-size: 56px; line-height: 50px; color: var(--white); letter-spacing: -1px; }
  .footer-mark .tagline { font-family: "Roboto Condensed", Arial, sans-serif; font-weight: 700; font-size: 18px; line-height: 16px; color: var(--white); margin-top: 6px; }
  .copyright { position: absolute; left: 0; width: 1200px; top: 78px; text-align: center; font-size: 6.5px; color: #8a8a8a; letter-spacing: .5px; }
</style>
</head>
<body>
<div class="canvas">

  <header class="topbar">
    <div class="brand">TKL<span class="sep">|</span>THE KINDRED LANTERN</div>
    <nav class="nav">
      <span class="item">WHO WE ARE</span>
      <span class="item">DONATE NOW!</span>
      <span class="item">LOGIN</span>
      <span class="item">CONTACT US</span>
      <span class="item">FIND US ON</span>
      <div class="social">
        <span></span><span></span><span></span><span></span><span></span><span></span>
      </div>
    </nav>
  </header>

  <div class="hero-backdrop" role="img" aria-label="Dimmed city plaza with towering billboards behind the content panel"></div>

  <main class="content">
    <section class="col col-welcome">
      <h2>WELCOME TO TKL</h2>
      <p>Lorem ipsum dolor sit amet, consectetur adipiscing elit. Sed sollicitudin aliquam neque. Suspendisse potenti. Phasellus nec vulputate ipsum. Phasellus tincidunt ante non elit laoreet sollicitudin. Cras diam sem, sollicitudin eu dictum ac, convallis vel ante. In lobortis, risus ac dignissim euismod, enim sapien dictum lorem, et tempus mi felis sit amet nibh. Pellentesque varius semper enim ac aliquet. In hac habitasse platea dictumst.</p>
      <p>Aliquam vitae nunc in nibh accumsan varius sed a nulla. Sed non pellentesque ligula. Sed dignissim imperdiet purus at fringilla. Cum sociis natoque penatibus et magnis dis parturient montes, nascetur ridiculus mus. Nulla blandit magna vitae turpis dictum ornare. Donec tempor iaculis velit, vitae interdum mauris luctus id. Vestibulum aliquet massa ac lorem laoreet elementum scelerisque leo cursus. Donec hendrerit mollis urna in blandit.</p>
    </section>

    <section class="col col-work">
      <h2>SAMPLE WORK1</h2>
      <p>Lorem ipsum dolor sit amet, consectetur adipiscing elit. Sed sollicitudin aliquam neque. Suspendisse potenti. Phasellus nec vulputate ipsum. Phasellus tincidunt ante non elit laoreet sollicitudin. Cras diam sem, sollicitudin eu dictum ac, convallis vel ante.</p>
      <h2 class="second">SAMPLE WORK2</h2>
      <p>Lorem ipsum dolor sit amet, consectetur adipiscing elit. Sed sollicitudin aliquam neque. Suspendisse potenti. Phasellus nec vulputate ipsum. Phasellus tincidunt ante non elit laoreet sollicitudin. Cras diam sem, sollicitudin eu dictum ac, convallis vel ante.</p>
    </section>

    <section class="col col-video">
      <h2>SAMPLE WORK3</h2>
      <div class="player">
        <div class="screen" role="img" aria-label="Video still of a busy plaza lit with billboards">
          <svg class="play" width="30" height="32" viewBox="0 0 30 32" aria-hidden="true"><path d="M2 2 L28 16 L2 30 Z" fill="#e8e8e8"/></svg>
          <div class="label">PLAY VIDEO</div>
        </div>
        <div class="controls">
          <svg width="5" height="6" viewBox="0 0 5 6" aria-hidden="true"><path d="M0 0 L5 3 L0 6 Z" fill="#111"/></svg>
          <div class="track"><i></i></div>
          <span>00:13 / 02:06</span>
          <svg width="9" height="7" viewBox="0 0 9 7" aria-hidden="true"><path d="M0 2 H2 L5 0 V7 L2 5 H0 Z" fill="#111"/><rect x="6" y="2" width="3" height="3" fill="#111"/></svg>
        </div>
      </div>
    </section>
  </main>

  <div class="divider-red"></div>
  <div class="close-tab">Click here to close
    <svg width="7" height="6" viewBox="0 0 7 6" aria-hidden="true"><path d="M0 6 L3.5 0 L7 6 Z" fill="#fff"/></svg>
  </div>

  <div class="city" role="img" aria-label="A child stands in a busy city plaza, looking up at towering advertising screens while taxis rush past"></div>
  <div class="divider-white"></div>

  <footer class="footer">
    <div class="footer-mark">
      <div class="initials">TKL</div>
      <div class="tagline">THE<br>KINDRED<br>LANTERN</div>
    </div>
    <div class="copyright">© 2011 TKL. All rights reserved.</div>
  </footer>

</div>
</body>
</html>
```